Oil and Gas Exploration and Production company needs a business card design

We need a business card design using our logo and colors in the logo. We want a mainstream design.

```html
<!DOCTYPE html>
<html lang="en">
<head>
<meta charset="utf-8">
<title>Solara Energy – Business Card</title>
<link rel="stylesheet" href="https://fonts.googleapis.com/css2?family=Arimo:wght@400;700&display=swap">
<style>
  :root {
    --backdrop: #e9e6e1;
    --card-white: #f4f4f2;
    --card-black: #050505;
    --ink: #111111;
    --gold: #e0bd3a;
    --white: #ffffff;
  }
  * { box-sizing: border-box; margin: 0; padding: 0; }
  html, body { width: 1200px; height: 780px; overflow: hidden; }
  body {
    background: var(--backdrop);
    font-family: "Arimo", Arial, sans-serif;
    display: flex; align-items: center; justify-content: center;
  }
  .business-card {
    width: 880px; height: 500px;
    border-radius: 26px;
    overflow: hidden;
    display: flex;
    box-shadow: 0 18px 40px rgba(0,0,0,.25);
  }
  .brand-panel {
    flex: 0 0 470px;
    background: var(--card-white);
    display: flex; align-items: center; justify-content: center;
    gap: 16px;
    padding: 0 40px;
  }
  .brand-dot {
    width: 30px; height: 30px; border-radius: 50%;
    background: var(--gold);
    flex: 0 0 30px;
  }
  .brand-name {
    font-family: "Arimo", Arial, sans-serif;
    font-weight: 700;
    font-size: 46px; line-height: 1;
    color: var(--ink);
    white-space: nowrap;
  }
  .contact-panel {
    flex: 1;
    background: var(--card-black);
    color: var(--white);
    padding: 92px 40px 0 58px;
  }
  .person-name { font-size: 34px; font-weight: 700; line-height: 1; }
  .person-title { font-size: 22px; color: var(--gold); margin-top: 6px; }
  .address { margin-top: 58px; font-size: 22px; line-height: 1.3; }
  .contact-list { list-style: none; margin-top: 4px; }
  .contact-list li {
    display: flex; align-items: center; gap: 12px;
    font-size: 22px; line-height: 1.4;
    white-space: nowrap;
  }
  .contact-icon {
    width: 24px; height: 24px; border-radius: 50%;
    background: var(--gold);
    display: flex; align-items: center; justify-content: center;
    flex: 0 0 24px;
  }
  .contact-icon svg { width: 14px; height: 14px; }
</style>
</head>
<body>
  <article class="business-card">
    <section class="brand-panel">
      <span class="brand-dot"></span>
      <span class="brand-name">Solara Energy</span>
    </section>
    <section class="contact-panel">
      <h1 class="person-name">Daniel Hart</h1>
      <p class="person-title">President &amp; CEO</p>
      <p class="address">PO BOX 456, Elm Road<br>4th Lane, Leeds</p>
      <ul class="contact-list">
        <li>
          <span class="contact-icon">
            <svg viewBox="0 0 16 16"><path d="M3 1h3l1.5 4-2 1.3a9 9 0 0 0 4.2 4.2L11 8.5l4 1.5v3a2 2 0 0 1-2 2A12 12 0 0 1 1 3a2 2 0 0 1 2-2z" fill="#050505"/></svg>
          </span>
          (123) 555 0182
        </li>
        <li>
          <span class="contact-icon">
            <svg viewBox="0 0 16 16"><rect x="1" y="3" width="14" height="10" rx="1" fill="#050505"/><path d="M1.5 3.5 8 9l6.5-5.5" stroke="#e0bd3a" stroke-width="1.4" fill="none"/></svg>
          </span>
          hello@solaraenergy.com
        </li>
        <li>
          <span class="contact-icon">
            <svg viewBox="0 0 16 16" fill="none" stroke="#050505" stroke-width="1.4"><circle cx="8" cy="8" r="6.5"/><ellipse cx="8" cy="8" rx="3" ry="6.5"/><path d="M1.5 8h13"/></svg>
          </span>
          www.solaraenergy.com
        </li>
      </ul>
    </section>
  </article>
</body>
</html>
```